Profesional personal website needs design and business card

I need a business card with my professional name as a logo "Dorian Vitality" for my business. I am a Wellness Coach, consultant and trainer. So it should be professional, wellness oriented and modern.

Target Market(s)

Private clients, governments, corporations. Luxury and high market.

Industry/Entity Type

Health And Wellness

Contact Information for Business Card

Dorian Vitality should be the logo

Colors

Designer to choose colors to be used in the design.

Requirements
Must have
• Dorian Vitality
• Name: Tomás Lirandel
• Wellness Coach, Consultant & Trainer.
• Website: www.dorianvitality-example.com
• Phone:
• Spain (+34) 612 480 317
• (USA) +1 (555) 610 4829
Nice to have
• The most important is the design of "Dorian Vitality", as this is going to be my personal brand logo. It should be professional, wellness, high end and actual.
Should not have
• no golds, no baroque style..

```html
<!DOCTYPE html>
<html lang="en">
<head>
<meta charset="utf-8">
<title>Dorian Vitality — Business Card</title>
<link rel="stylesheet" href="https://fonts.googleapis.com/css2?family=Bebas+Neue&display=swap">
<style>
  :root {
    --backdrop: #0b0b0b;
    --card: #2a2a2b;
    --card-back: #282829;
    --lime: #6cb51b;
    --white: #f2f2f2;
    --emboss: #4a4a4c;
    --emboss-light: #58585a;
  }
  * { margin: 0; padding: 0; box-sizing: border-box; }
  html, body {
    width: 1200px;
    height: 822px;
    overflow: hidden;
    background: var(--backdrop);
  }
  .stage {
    width: 1200px;
    height: 822px;
    display: flex;
    align-items: center;
    justify-content: center;
    gap: 60px;
    font-family: "Bebas Neue", "Oswald", sans-serif;
  }
  .card {
    width: 520px;
    height: 298px;
    border: 2px solid var(--lime);
    border-radius: 3px;
    display: flex;
    flex-direction: column;
    align-items: center;
    justify-content: center;
    box-shadow: 0 18px 40px rgba(0, 0, 0, 0.6);
  }
  .card-front { background: var(--card); padding-top: 8px; }
  .card-back { background: var(--card-back); }

  .brand-mark {
    width: 84px;
    height: 84px;
    border-radius: 50%;
    border: 5px solid var(--lime);
    margin-bottom: 10px;
  }
  .brand-name {
    color: var(--white);
    font-size: 46px;
    line-height: 1;
    letter-spacing: 0.5px;
  }
  .person-name {
    color: var(--lime);
    font-size: 27px;
    line-height: 1;
    margin-top: 16px;
    letter-spacing: 0.3px;
  }
  .person-role {
    color: var(--white);
    font-size: 15px;
    line-height: 1;
    margin-top: 4px;
    letter-spacing: 0.3px;
  }
  .contact-line {
    color: var(--white);
    font-size: 15px;
    line-height: 1;
    margin-top: 20px;
    letter-spacing: 0.3px;
    white-space: nowrap;
  }
  .contact-line .label,
  .contact-line .domain { color: var(--lime); }
  .contact-line .sep { margin: 0 6px; }

  .back-mark {
    width: 96px;
    height: 96px;
    border-radius: 50%;
    border: 5px solid var(--emboss-light);
    margin-bottom: 12px;
  }
  .back-name {
    color: var(--emboss);
    font-size: 50px;
    line-height: 1;
    letter-spacing: 0.5px;
  }
</style>
</head>
<body>
  <main class="stage">
    <section class="card card-front" aria-label="Business card front">
      <div class="brand-mark" aria-hidden="true"></div>
      <h1 class="brand-name">Dorian Vitality</h1>
      <p class="person-name">Tomás Lirandel</p>
      <p class="person-role">Wellness Coach, Consultant &amp; Trainer</p>
      <p class="contact-line">
        <span class="label">Spain</span> (+34) 612 480 317<span class="sep">|</span><span class="label">(USA)</span> +1 (555) 610 4829<span class="sep">|</span>www.<span class="domain">dorianvitality-example</span>.com
      </p>
    </section>

    <section class="card card-back" aria-label="Business card back">
      <div class="back-mark" aria-hidden="true"></div>
      <p class="back-name">Dorian Vitality</p>
    </section>
  </main>
</body>
</html>
```